Upmarket Dessert Lounge needs a Business Card Design

We are an upmarket dessert lounge needing a business card to match our image.

We want something that is simple yet beautiful, feminine, classy, sophisticated and elegant. We want it to stand out and don't mind if it is bold.

The design should include our logo and colours of red or maroon with gold highlights. We don't mind if black is used.

Marlow & Quince

Target Market(s)

For those who like to indulge or treat themselves and give in to their temptations on good quality desserts.

Industry/Entity Type

Business

Requirements
Must have
• Must include our logo and our name

Marlow & Quince

M & Q

```html
<!DOCTYPE html>
<html lang="en">
<head>
<meta charset="utf-8">
<title>Marlow &amp; Quince – Business Card</title>
<link rel="stylesheet" href="https://fonts.googleapis.com/css2?family=Source+Sans+3:wght@400;600&display=swap">
<style>
  :root {
    --backdrop: #9a6a45;
    --card-black: #242021;
    --maroon: #6a1214;
    --cream: #f4d2a2;
    --font-text: "Source Sans 3", Arial, sans-serif;
  }
  * { box-sizing: border-box; margin: 0; padding: 0; }
  html, body {
    width: 1200px; height: 402px; overflow: hidden;
    background: var(--backdrop);
    font-family: var(--font-text);
    color: var(--cream);
  }
  .stage { position: relative; width: 1200px; height: 402px; }
  .card {
    position: absolute; top: 56px;
    width: 511px; height: 290px;
    border-radius: 16px; overflow: hidden;
    background: var(--card-black);
  }
  .card--front { left: 54px; }
  .card--back { left: 640px; display: flex; align-items: center; justify-content: center; }

  .front-brand {
    position: absolute; top: 0; left: 0; right: 0; height: 171px;
    display: flex; align-items: center; justify-content: center;
    font-size: 30px; font-weight: 400; letter-spacing: 2px;
    text-transform: uppercase;
  }
  .info-band {
    position: absolute; left: 0; right: 0; top: 171px; bottom: 0;
    background: var(--maroon);
    border-top: 2px solid var(--cream);
  }
  .band-notch { position: absolute; left: 108px; top: -2px; }
  .holder {
    position: absolute; left: 0; width: 255px; top: 60px;
    text-align: center; font-size: 15px;
  }
  .holder strong { font-weight: 600; font-size: 16px; }
  .divider {
    position: absolute; left: 255px; top: 10px; bottom: 8px;
    width: 1px; background: var(--cream);
  }
  .contact {
    position: absolute; left: 274px; top: 8px;
    font-size: 13px; line-height: 15px;
  }
  .contact__address { margin-bottom: 8px; }
  .contact__row { display: flex; align-items: center; gap: 5px; height: 18px; }
  .contact__row svg { width: 9px; height: 9px; flex: none; }

  .back-monogram {
    font-size: 86px; font-weight: 400; letter-spacing: 2px; line-height: 1;
  }
</style>
</head>
<body>
<main class="stage">
  <section class="card card--front" aria-label="Card front">
    <div class="front-brand">Marlow &amp; Quince</div>
    <div class="info-band">
      <svg class="band-notch" width="22" height="14" viewBox="0 0 22 14" aria-hidden="true">
        <path d="M0 1 L11 13 L22 1" fill="var(--card-black)" stroke="var(--cream)" stroke-width="2"/>
      </svg>
      <p class="holder"><strong>Your name,</strong> Title</p>
      <div class="divider"></div>
      <div class="contact">
        <p class="contact__address">Street Name, City Name<br>State Zip Code</p>
        <p class="contact__row">
          <svg viewBox="0 0 10 10" aria-hidden="true"><circle cx="5" cy="5" r="4.3" fill="none" stroke="var(--cream)" stroke-width="1.2"/><path d="M3.3 2.6 L4.3 3.8 L3.8 4.6 Q4.6 6 5.6 6.3 L6.3 5.8 L7.4 6.8 Q6.6 8 5.4 7.4 Q3 6.2 2.6 3.6 Z" fill="var(--cream)"/></svg>
          555-014-2270</p>
        <p class="contact__row">
          <svg viewBox="0 0 10 10" aria-hidden="true"><rect x="2.5" y="0.5" width="5" height="9" rx="1" fill="none" stroke="var(--cream)" stroke-width="1.2"/><rect x="3.6" y="2" width="2.8" height="3" fill="var(--cream)"/></svg>
          555-014-2270</p>
        <p class="contact__row">
          <svg viewBox="0 0 10 10" aria-hidden="true"><rect x="0.5" y="2" width="9" height="6" fill="var(--cream)"/><path d="M0.5 2 L5 5.5 L9.5 2" fill="none" stroke="var(--maroon)" stroke-width="1"/></svg>
          info@marlowquince.com</p>
        <p class="contact__row">
          <svg viewBox="0 0 10 10" aria-hidden="true"><circle cx="5" cy="5" r="4.3" fill="none" stroke="var(--cream)" stroke-width="1.1"/><ellipse cx="5" cy="5" rx="1.8" ry="4.3" fill="none" stroke="var(--cream)" stroke-width="0.9"/><path d="M0.7 5 H9.3" stroke="var(--cream)" stroke-width="0.9"/></svg>
          www.marlowquince.com</p>
      </div>
    </div>
  </section>

  <section class="card card--back" aria-label="Card back">
    <p class="back-monogram">M &amp; Q</p>
  </section>
</main>
</body>
</html>
```